Business Card - Tidal Lanes

Need Business Card design for company named Tidal Lanes. Software development focused mainly on Brindle Orvix & Zelt Apps. I've attached our logo with both a black and white background. Please add trademark symbol to logo when using.

```html
<!DOCTYPE html>
<html lang="en">
<head>
<meta charset="utf-8">
<title>Tidal Lanes – Business Card</title>
<link rel="stylesheet" href="https://fonts.googleapis.com/css2?family=Open+Sans:wght@400;600;700&display=swap">
<style>
  :root {
    --backdrop: #e8e3da;
    --card-white: #ffffff;
    --ink: #1a1a1a;
    --black: #000000;
    --brand-yellow: #f9c312;
    --brand-orange: #f59a38;
    --brand-red: #d81f2a;
  }
  * { margin: 0; padding: 0; box-sizing: border-box; }
  html, body {
    width: 1200px; height: 1014px; overflow: hidden;
    background: var(--backdrop);
    font-family: "Open Sans", sans-serif;
  }
  .sheet {
    width: 1200px; height: 1014px;
    display: flex; flex-direction: column; align-items: center; justify-content: center;
    gap: 64px;
  }
  .card {
    position: relative;
    width: 700px; height: 400px;
    background: var(--card-white);
    overflow: hidden;
    box-shadow: 0 6px 18px rgba(0,0,0,0.18);
  }
  .card-front__panel { position: absolute; inset: 0; }
  .brand {
    position: absolute;
    display: flex; align-items: center; gap: 14px;
    color: #fff; font-weight: 600;
  }
  .card-front .brand { left: 44px; top: 176px; font-size: 38px; letter-spacing: -0.5px; }
  .brand__dot { width: 22px; height: 22px; border-radius: 50%; background: var(--brand-yellow); flex: none; }
  .brand__tm { font-size: 0.4em; vertical-align: super; }
  .contact {
    position: absolute; right: 40px; top: 36px;
    text-align: right; color: var(--ink);
  }
  .contact__name { font-size: 27px; font-weight: 700; line-height: 1.15; }
  .contact__role { font-size: 21px; font-weight: 700; color: var(--brand-red); line-height: 1.15; }
  .contact__lines { margin-top: 46px; font-size: 19px; line-height: 1.5; }
  .card-back .brand {
    left: 0; right: 0; top: 120px; justify-content: center;
    color: var(--ink); font-size: 64px; font-weight: 600; letter-spacing: -1px;
  }
  .card-back .brand__dot { width: 40px; height: 40px; background: var(--brand-red); }
  .card-back__url {
    position: absolute; left: 48px; bottom: 36px;
    font-size: 24px; font-weight: 700; color: var(--ink);
  }
</style>
</head>
<body>
<main class="sheet">
  <section class="card card-front" aria-label="Business card front">
    <svg class="card-front__panel" viewBox="0 0 700 400" width="700" height="400" aria-hidden="true">
      <path class="band-yellow" fill="var(--brand-yellow)"
        d="M0 0 H296 V120 Q296 140 316 146 L330 150 Q352 156 352 180 V400 H0 Z"/>
      <path class="panel-black" fill="var(--black)"
        d="M0 0 H266 V128 Q266 152 288 160 L302 165 Q322 172 322 196 V400 H0 Z"/>
    </svg>
    <div class="brand"><span class="brand__dot"></span><span>Tidal Lanes<span class="brand__tm">™</span></span></div>
    <div class="contact">
      <p class="contact__name">Owen Castell</p>
      <p class="contact__role">Manager</p>
      <div class="contact__lines">
        <p>555-214-7730 Mobile</p>
        <p>owen@tidallanes.com</p>
        <p>2140 Harbor Row</p>
        <p>Dunmore, FL 30412</p>
        <p>555-214-7731 Fax</p>
      </div>
    </div>
  </section>

  <section class="card card-back" aria-label="Business card back">
    <div class="brand"><span class="brand__dot"></span><span>Tidal Lanes</span></div>
    <p class="card-back__url">tidallanes.com</p>
  </section>
</main>
</body>
</html>
```